Stylish Business Cards Wanted

- DOUBLE SIDED Design Required -

High end, edgy cards for a corporate and personal stylist. Must include logo,
Name: Belinda Harwick
Title: Director and Stylist
telephone : +61 8 7142 5809
email: belinda@theloombriefing.example
website: theloombriefing.example
Tag: Corporate Workwear & Uniform Specialist | Personal Stylist
Would like nice icons for telephone, email, website

Target Market(s)

Businesses wanting stylish uniforms, people wanting stylish wardrobes

Industry/Entity Type

Corporate Workwear Stylist

Contact Information for Business Card

I would like black, white and gold foiling incorporated in the design - possibly a touch of the other colours on my branding guide attached Name: Belinda Harwick Title: Director and Stylist telephone : +61 8 7142 5809 email: belinda@theloombriefing.example website: theloombriefing.example Tag: Corporate Workwear & Uniform Specialist | Personal Stylist Would like nice icons for telephone, email, website

Font styles to use
Other font styles liked:
• Raleway

Colors

Designer to choose colors to be used in the design.

Requirements
Must have
• Gold foil accents

```html
<!DOCTYPE html>
<html lang="en">
<head>
<meta charset="utf-8">
<title>The Loom Briefing — Business Cards</title>
<link rel="stylesheet" href="https://fonts.googleapis.com/css2?family=Montserrat:wght@400;500;600;700&display=swap">
<style>
  :root {
    --backdrop: #1a1a1a;
    --card: #232323;
    --white: #ffffff;
    --soft-white: #e9e9e9;
    --magenta: #e5177b;
  }
  * { margin: 0; padding: 0; box-sizing: border-box; }
  html, body {
    width: 1200px;
    height: 988px;
    overflow: hidden;
    background: var(--backdrop);
    font-family: "Montserrat", sans-serif;
  }
  .canvas {
    position: relative;
    width: 1200px;
    height: 988px;
  }
  .card {
    position: absolute;
    width: 560px;
    height: 320px;
    background: var(--card);
    box-shadow: 0 14px 30px rgba(0, 0, 0, 0.55);
  }
  .card--front { left: 50px; top: 110px; }
  .card--back { left: 590px; top: 558px; }

  /* Front */
  .brand {
    position: absolute;
    left: 0; right: 0; top: 104px;
    display: flex;
    align-items: center;
    justify-content: center;
    gap: 14px;
  }
  .brand__mark {
    width: 14px; height: 14px;
    background: var(--magenta);
  }
  .brand__name {
    color: var(--white);
    font-weight: 600;
    font-size: 38px;
    letter-spacing: 0.5px;
  }
  .tagline {
    position: absolute;
    left: 0; right: 0; bottom: 44px;
    text-align: center;
    color: var(--magenta);
    font-size: 14.5px;
    font-weight: 500;
    letter-spacing: 0.3px;
  }

  /* Back */
  .person {
    position: absolute;
    right: 318px;
    top: 136px;
    text-align: right;
  }
  .person__name {
    color: var(--magenta);
    font-weight: 700;
    font-size: 24px;
    letter-spacing: 1px;
    text-transform: uppercase;
    white-space: nowrap;
  }
  .person__title {
    color: var(--soft-white);
    font-size: 14px;
    margin-top: 2px;
  }
  .divider {
    position: absolute;
    left: 262px;
    top: 112px;
    width: 1.5px;
    height: 96px;
    background: var(--magenta);
  }
  .contacts {
    position: absolute;
    left: 282px;
    top: 108px;
    list-style: none;
  }
  .contacts__item {
    display: flex;
    align-items: center;
    gap: 8px;
    color: var(--soft-white);
    font-size: 13.5px;
    line-height: 1;
    margin-bottom: 12px;
    white-space: nowrap;
  }
  .contacts__item--phone {
    color: var(--white);
    font-weight: 600;
    font-size: 17px;
  }
  .contacts__icon { width: 14px; height: 14px; flex: none; fill: var(--magenta); }
</style>
</head>
<body>
<main class="canvas">

  <section class="card card--front" aria-label="Card front">
    <div class="brand">
      <span class="brand__mark"></span>
      <span class="brand__name">The Loom Briefing</span>
    </div>
    <p class="tagline">Corporate Workwear &amp; Uniform Specialist | Personal Stylist</p>
  </section>

  <section class="card card--back" aria-label="Card back">
    <div class="person">
      <h1 class="person__name">Belinda Harwick</h1>
      <p class="person__title">Director and Stylist</p>
    </div>
    <span class="divider"></span>
    <ul class="contacts">
      <li class="contacts__item contacts__item--phone">
        <svg class="contacts__icon" viewBox="0 0 24 24" aria-hidden="true"><path d="M6.6 10.8a15.1 15.1 0 0 0 6.6 6.6l2.2-2.2c.3-.3.7-.4 1-.2 1.1.4 2.3.6 3.6.6.6 0 1 .4 1 1V20c0 .6-.4 1-1 1A17 17 0 0 1 3 4c0-.6.4-1 1-1h3.5c.6 0 1 .4 1 1 0 1.3.2 2.5.6 3.6.1.3 0 .7-.2 1z"/></svg>
        +61 8 7142 5809
      </li>
      <li class="contacts__item">
        <svg class="contacts__icon" viewBox="0 0 24 24" aria-hidden="true"><path d="M2 5h20v14H2z M2 5l10 8 10-8" fill="none" stroke="#e5177b" stroke-width="2"/></svg>
        belinda@theloombriefing.example
      </li>
      <li class="contacts__item">
        <svg class="contacts__icon" viewBox="0 0 24 24" aria-hidden="true"><circle cx="12" cy="12" r="9" fill="none" stroke="#e5177b" stroke-width="2"/><path d="M3 12h18M12 3c3 3 3 15 0 18M12 3c-3 3-3 15 0 18" fill="none" stroke="#e5177b" stroke-width="1.6"/></svg>
        www.theloombriefing.example
      </li>
    </ul>
  </section>

</main>
</body>
</html>
```